Quorva - corporate Business Card

We need a good look and innovative business card for a new start up company based in Los Angeles called "Quorva". We are in a payment business, including payment card, app, and ewallet. We are expert in online payment and Card not present (CNP) transaction.
We need an innovative, modern business card.

Our logo font is Aero Matics

Target Market(s)

Startup - Bank - Online Payment - Card Manufacturing

Industry/Entity Type

Startup

Contact Information for Business Card

phone: 555 014 7396 - Address: 4172 Marlowe blvd, Denfield, NV 89017

Requirements
Must have
• Message: innovative, professional, expert, high tech, trust, online payment expert, security
Nice to have
• no comment
Should not have
• no Comment

```html
<!DOCTYPE html>
<html lang="en">
<head>
<meta charset="UTF-8">
<title>Quorva – Business Card</title>
<link href="https://fonts.googleapis.com/css2?family=Lato:wght@400;700&display=swap" rel="stylesheet">
<style>
  :root {
    --page-bg: #ebe8e5;
    --card-red: #b91e2e;
    --card-white: #ffffff;
    --window-light: #f1ecec;
    --window-mid: #e3dada;
    --window-edge: rgba(255, 255, 255, 0.75);
  }
  * { margin: 0; padding: 0; box-sizing: border-box; }
  html, body {
    width: 1200px;
    height: 900px;
    overflow: hidden;
    background: var(--page-bg);
    font-family: "Lato", sans-serif;
  }
  .business-card {
    position: absolute;
    left: 150px;
    top: 173px;
    width: 900px;
    height: 554px;
    background: var(--card-red);
    color: var(--card-white);
    box-shadow: 0 10px 30px rgba(0, 0, 0, 0.12);
  }
  .frosted-window {
    position: absolute;
    left: 26px;
    top: 62px;
    width: 446px;
    height: 446px;
    border-radius: 50%;
    background: radial-gradient(circle at 45% 40%, var(--window-light) 0%, var(--window-mid) 100%);
    box-shadow: inset 0 0 0 2px var(--window-edge), inset 0 0 18px rgba(120, 60, 60, 0.18);
  }
  .brand {
    position: absolute;
    left: 47px;
    top: 238px;
    display: flex;
    align-items: center;
    gap: 24px;
  }
  .brand-dot {
    width: 94px;
    height: 94px;
    border-radius: 50%;
    background: var(--card-red);
    flex-shrink: 0;
  }
  .brand-name {
    font-family: "Lato", sans-serif;
    font-weight: 400;
    font-size: 72px;
    line-height: 1;
    color: var(--card-red);
    letter-spacing: 1px;
  }
  .contact {
    position: absolute;
    left: 523px;
    top: 124px;
  }
  .contact-name {
    font-weight: 700;
    font-size: 27px;
    letter-spacing: 0.5px;
    text-transform: uppercase;
    line-height: 1.2;
  }
  .contact-role {
    font-size: 24px;
    line-height: 1.3;
    margin-top: 2px;
  }
  .contact-lines {
    list-style: none;
    margin-top: 28px;
  }
  .contact-lines li {
    display: flex;
    align-items: center;
    gap: 10px;
    font-size: 24px;
    line-height: 37px;
  }
  .contact-lines svg {
    width: 20px;
    height: 20px;
    flex-shrink: 0;
  }
  .contact-address {
    font-style: normal;
    font-size: 24px;
    line-height: 33px;
    margin-top: 28px;
  }
</style>
</head>
<body>
  <div class="business-card">
    <div class="frosted-window" role="img" aria-label="Frosted transparent circle window"></div>
    <div class="brand">
      <span class="brand-dot"></span>
      <span class="brand-name">quorva</span>
    </div>

    <div class="contact">
      <div class="contact-name">Marcus Delaney</div>
      <div class="contact-role">Managing Director</div>

      <ul class="contact-lines">
        <li>
          <svg viewBox="0 0 24 24" aria-hidden="true"><path fill="#ffffff" d="M6.6 10.8a15.1 15.1 0 0 0 6.6 6.6l2.2-2.2c.3-.3.7-.4 1-.2 1.1.4 2.3.6 3.6.6.6 0 1 .4 1 1V20c0 .6-.4 1-1 1A17 17 0 0 1 3 4c0-.6.4-1 1-1h3.5c.6 0 1 .4 1 1 0 1.3.2 2.5.6 3.6.1.3 0 .7-.2 1z"/></svg>
          555 014 7396
        </li>
        <li>
          <svg viewBox="0 0 24 24" aria-hidden="true"><rect x="2" y="5" width="20" height="14" fill="#ffffff"/><path d="M3.5 6.5 12 13l8.5-6.5" fill="none" stroke="#b91e2e" stroke-width="1.6"/></svg>
          hello@quorvamail.com
        </li>
        <li>
          <svg viewBox="0 0 24 24" aria-hidden="true"><circle cx="12" cy="12" r="9.5" fill="#ffffff"/><path d="M2.5 12h19M12 2.5c3 3 3 16 0 19M12 2.5c-3 3-3 16 0 19" fill="none" stroke="#b91e2e" stroke-width="1.4"/></svg>
          www.quorvapay.com
        </li>
      </ul>

      <address class="contact-address">
        4172 Marlowe blvd,<br>
        Denfield, NV 89017
      </address>
    </div>
  </div>
</body>
</html>
```